Awesome photographers card for an awesome new business

Double sided business card Black background and silver logo in middle on one side. Details on otherside. please keep it simple

Industry/Entity Type

Photographer

Contact Information for Business Card

Gerald Fenwick
0452817360
GeraldFenwickPhotography47@mailbox.test
www.GeraldFenwickPhotography.test.au
Instagram _Gerald_fenwick

Requirements
Must have
• My logo in Silver
• please use instagram logo instead of "Instagram"

```html
<!DOCTYPE html>
<html lang="en">
<head>
<meta charset="utf-8">
<title>Gerald Fenwick Photography – Business Card</title>
<link rel="stylesheet" href="https://fonts.googleapis.com/css2?family=Roboto:wght@400;500&family=Roboto+Condensed:wght@500&display=swap">
<style>
  :root{
    --stage:#2b2b2d;
    --front-dark:#6e6e6e;
    --front-mid:#b4b4b4;
    --front-light:#f1f1f1;
    --ink-white:#ffffff;
    --ink-grey:#7a7a7a;
    --back-card:#1d1e20;
    --silver:#c9c9c9;
  }
  *{margin:0;padding:0;box-sizing:border-box}
  html,body{width:1200px;height:960px;overflow:hidden;background:var(--stage)}
  .canvas{position:relative;width:1200px;height:960px}
  .card{position:absolute;width:600px;height:342px;overflow:hidden}
  .card-front{left:314px;top:113px;
    background:radial-gradient(ellipse 320px 260px at 230px 180px,var(--front-mid),var(--front-dark) 90%)}
  .card-front .disc{position:absolute;left:0;top:0}
  .holder-name{position:absolute;left:32px;top:38px;font:500 21px/1 "Roboto Condensed",sans-serif;color:var(--ink-white);text-transform:uppercase}
  .contact{position:absolute;left:32px;top:234px;list-style:none;font:400 14px/19px "Roboto",sans-serif;color:var(--ink-white)}
  .contact .social{display:flex;align-items:center;gap:8px}
  .contact .social i{display:inline-block;width:14px;height:14px;background:var(--ink-white);border-radius:2px}
  .brand-mark{position:absolute;display:flex;flex-direction:column;align-items:center;justify-content:center;text-align:center;font-family:"Roboto",sans-serif;font-weight:500}
  .card-front .brand-mark{left:391px;top:95px;width:140px;height:140px;border:3px solid var(--ink-grey);border-radius:50%;color:var(--ink-grey);font-size:14px;line-height:18px}
  .card-back{left:312px;top:475px;background:var(--back-card)}
  .card-back .brand-mark{left:211px;top:73px;width:176px;height:176px;border:3px solid var(--silver);border-radius:50%;color:var(--silver);font-size:17px;line-height:22px}
  .back-url{position:absolute;left:0;right:0;top:288px;text-align:center;font:400 15px/1 "Roboto",sans-serif;letter-spacing:2px;color:var(--ink-white)}
</style>
</head>
<body>
<div class="canvas">
  <section class="card card-front">
    <svg class="disc" width="600" height="342" viewBox="0 0 600 342" aria-hidden="true">
      <circle cx="452" cy="172" r="168" fill="var(--front-light)"/>
    </svg>
    <h1 class="holder-name">Gerald Fenwick</h1>
    <ul class="contact">
      <li>0452817360</li>
      <li>GeraldFenwickPhotography47@mailbox.test</li>
      <li>www.GeraldFenwickPhotography.test.au</li>
      <li class="social"><i></i>_Gerald_fenwick</li>
    </ul>
    <div class="brand-mark">Gerald<br>Fenwick<br>Photography</div>
  </section>
  <section class="card card-back">
    <div class="brand-mark">Gerald<br>Fenwick<br>Photography</div>
    <p class="back-url">www.GeraldFenwickPhotography.test.au</p>
  </section>
</div>
</body>
</html>
```